Heron Loan Partners Business Card

We need a business card design for our mortgage servicing company. In addition to servicing the loans of homeowners, we help homeowners with purchasing their homes and any mortgage refinancing. We would like to see designs that use the colors in the logo attached below (gold-ish yellow and navy blue), and any other design you deem fit! The design should communicate a simpler life with smart mortgages provided by Heron.

```html
<!DOCTYPE html>
<html lang="en">
<head>
<meta charset="UTF-8">
<title>Heron Loan Partners Business Card</title>
<link href="https://fonts.googleapis.com/css2?family=Poppins:wght@400;500;600&family=Crimson+Text:wght@400&display=swap" rel="stylesheet">
<style>
  :root {
    --backdrop: #e4e5e7;
    --card: #ffffff;
    --navy: #231c4f;
    --gold: #d8aa36;
    --ink: #1c1c1f;
  }
  * { margin: 0; padding: 0; box-sizing: border-box; }
  html, body {
    width: 1200px;
    height: 900px;
    overflow: hidden;
    background: var(--backdrop);
  }
  .stage {
    position: relative;
    width: 1200px;
    height: 900px;
  }
  .card {
    position: absolute;
    top: 217px;
    width: 308px;
    height: 499px;
    background: var(--card);
    box-shadow: 3px 3px 4px rgba(0,0,0,0.35);
  }
  .card--front {
    left: 279px;
    border-radius: 0 60px 0 60px;
  }
  .card--back {
    left: 617px;
    border-radius: 60px 0 60px 0;
  }
  .brand {
    position: absolute;
    left: 0;
    width: 100%;
    display: flex;
    align-items: center;
    justify-content: center;
    gap: 8px;
    font-family: "Poppins", sans-serif;
    font-weight: 600;
    font-size: 21px;
    color: var(--navy);
    white-space: nowrap;
  }
  .brand__dot {
    width: 12px;
    height: 12px;
    border-radius: 50%;
    background: var(--gold);
    flex: none;
  }
  .card--front .brand { top: 236px; }
  .card--back .brand { top: 170px; }
  .person {
    position: absolute;
    left: 32px;
    top: 305px;
  }
  .person__name {
    font-family: "Crimson Text", serif;
    font-size: 22px;
    line-height: 1.1;
    color: var(--navy);
  }
  .person__first { color: var(--gold); }
  .person__role {
    font-family: "Poppins", sans-serif;
    font-size: 14px;
    color: var(--navy);
    line-height: 1.2;
  }
  .contacts {
    position: absolute;
    left: 32px;
    top: 358px;
    list-style: none;
    font-family: "Poppins", sans-serif;
    font-size: 14px;
    color: var(--ink);
  }
  .contacts li {
    display: flex;
    align-items: center;
    gap: 5px;
    height: 18px;
  }
  .contacts svg { width: 12px; height: 12px; flex: none; }
  .address {
    position: absolute;
    left: 32px;
    top: 427px;
    font-family: "Poppins", sans-serif;
    font-size: 14px;
    line-height: 18px;
    color: var(--ink);
    font-style: normal;
  }
</style>
</head>
<body>
<main class="stage">
  <section class="card card--front">
    <div class="brand"><span class="brand__dot"></span>Heron Loan Partners</div>
  </section>

  <section class="card card--back">
    <div class="brand"><span class="brand__dot"></span>Heron Loan Partners</div>

    <div class="person">
      <p class="person__name"><span class="person__first">Daniel</span> Reyes</p>
      <p class="person__role">Managing Director</p>
    </div>

    <ul class="contacts">
      <li>
        <svg viewBox="0 0 24 24" aria-hidden="true"><path fill="none" stroke="#d8aa36" stroke-width="2.4" d="M6 3l4 4-2 3c1 2 4 5 6 6l3-2 4 4-3 3C10 21 3 14 3 6z"/></svg>
        044-218 730 615
      </li>
      <li>
        <svg viewBox="0 0 24 24" aria-hidden="true"><rect x="2" y="5" width="20" height="14" fill="#d8aa36"/><path d="M2 5l10 8 10-8" fill="none" stroke="#fff" stroke-width="1.8"/></svg>
        hello@heronloan.com
      </li>
      <li>
        <svg viewBox="0 0 24 24" aria-hidden="true"><g fill="none" stroke="#d8aa36" stroke-width="2"><circle cx="12" cy="12" r="10"/><ellipse cx="12" cy="12" rx="4" ry="10"/><path d="M2 12h20M4 7h16M4 17h16"/></g></svg>
        www.heronloan.com
      </li>
    </ul>

    <address class="address">
      78, Harbour View Road<br>
      45310,Eastbrook
    </address>
  </section>
</main>
</body>
</html>
```